BRISKEL Need a luxury modern business card designed.

Need a luxury modern business card designed. refer to the uploaded files for the company name and logo in the zip file under source files. i will making my descion on monday. so please send in before then so if we need to edit we will have the time. we have a trade show coming up and im on a deadline for printer.

Target Market(s)

high end clients

Contact Information for Business Card

Company nAme and logo. Tobias Fennick Co-Founder / Project Manager Office # 555-318-7094 Cell # 555-642-1586 BRISKEL.CA Tobias@briskel-example.ca

Font styles to use
Other font styles liked:
• Modern

Requirements
Must have
• Company name and logo, contact info, using the black, gold and white color scheme.

```html
<!DOCTYPE html>
<html lang="en">
<head>
<meta charset="utf-8">
<title>BRISKEL Business Card</title>
<link href="https://fonts.googleapis.com/css2?family=Josefin+Sans:wght@300;400&family=Roboto:wght@400;700&display=swap" rel="stylesheet">
<style>
  :root {
    --backdrop: #676767;
    --card: #2e2e2e;
    --gold: #a8955a;
    --white: #f4f4f2;
    --rule: #4a4a4a;
  }
  html, body {
    margin: 0;
    width: 1200px;
    height: 866px;
    overflow: hidden;
    background: var(--backdrop);
  }
  .canvas {
    position: relative;
    width: 1200px;
    height: 866px;
    display: flex;
    align-items: center;
    justify-content: center;
    gap: 40px;
  }
  .card {
    position: relative;
    width: 520px;
    height: 297px;
    background: var(--card);
    border-bottom: 6px solid var(--gold);
    box-shadow: 0 10px 24px rgba(0,0,0,0.45);
    box-sizing: border-box;
    overflow: hidden;
  }
  .wordmark {
    font-family: "Josefin Sans", sans-serif;
    font-weight: 300;
    color: var(--white);
    letter-spacing: 0.14em;
    line-height: 1;
  }
  /* Front */
  .card-front .wordmark {
    position: absolute;
    right: 34px;
    top: 74px;
    font-size: 44px;
  }
  .contact {
    position: absolute;
    left: 30px;
    top: 140px;
    font-family: "Roboto", sans-serif;
    color: var(--white);
  }
  .contact-name {
    margin: 0;
    font-size: 17px;
    font-weight: 700;
    color: var(--gold);
    text-transform: uppercase;
    letter-spacing: 0.02em;
  }
  .contact-title {
    margin: 2px 0 10px;
    font-size: 14px;
  }
  .contact-list {
    list-style: none;
    margin: 0;
    padding: 0;
    font-size: 13.5px;
    line-height: 19px;
  }
  .contact-list li {
    display: flex;
    align-items: center;
    gap: 8px;
  }
  .contact-list svg {
    width: 12px;
    height: 12px;
    flex: none;
  }
  .contact-rule {
    position: absolute;
    left: 250px;
    right: 34px;
    top: 238px;
    height: 1px;
    background: var(--rule);
  }
  /* Back */
  .card-back {
    display: flex;
    align-items: center;
    justify-content: center;
  }
  .card-back .wordmark {
    font-size: 56px;
  }
</style>
</head>
<body>
<main class="canvas">
  <section class="card card-front" aria-label="Business card front">
    <div class="wordmark">BRISKEL</div>
    <div class="contact">
      <p class="contact-name">Tobias Fennick</p>
      <p class="contact-title">Co-Founder / Project Manager</p>
      <ul class="contact-list">
        <li>
          <svg viewBox="0 0 12 12" aria-hidden="true"><path d="M1 4 Q6 0 11 4 L9.5 5.5 L8 4.5 L4 4.5 L2.5 5.5 Z M3 6 H9 L10 11 H2 Z" fill="#a8955a"/></svg>
          555-318-7094
        </li>
        <li>
          <svg viewBox="0 0 12 12" aria-hidden="true"><rect x="3" y="0.5" width="6" height="11" rx="1" fill="none" stroke="#a8955a" stroke-width="1.2"/></svg>
          555-642-1586
        </li>
        <li>
          <svg viewBox="0 0 12 12" aria-hidden="true"><rect x="0.5" y="2" width="11" height="8" fill="#a8955a"/><path d="M0.5 2 L6 7 L11.5 2" fill="none" stroke="#2e2e2e" stroke-width="1"/></svg>
          briskel.ca tobias@briskel-example.ca
        </li>
      </ul>
    </div>
    <div class="contact-rule"></div>
  </section>
  <section class="card card-back" aria-label="Business card back">
    <div class="wordmark">BRISKEL</div>
  </section>
</main>
</body>
</html>
```